Brightmoor - a website to encourage people to spend time in nature

I have a squarespace site with some content on it but the squarespace template doesn't completely suit my needs, I keep fiddling with the template but actually I need some professional help to get it looking the way I want and with the right 'mood'.
The website is for "Brightmoor" - it will be a blog where I write about the importance of nature for good health. I also want to use the website to market services such as outdoor coaching, retreats and walking workshops.
This has been in my head for a LONG time and I currently only use instagram for micro-blogs but it's time for me to get this moving. I've previously engaged other designers on branding for it but they just didn't get it quite the way that I wanted it and I wasn't completely happy with the results. It's been a process for me as to what I want but in the meantime I just didn't come back to the design aspect of it now. I'm looking for a designer who understands the purpose of the website, the ethos and can help me realise this into a design that's clean, clear and simple.

Please note that I have a domain (brightmoor.org) and a lot of content drafted on squarespace already. I have published it with password protection - password is brightmoor2020 - it still has some of the original template on it, but does have some content. Don't take it as anything to follow in particular, i am looking for fresh eyes and fresh ideas.

Target Market(s)

There are three main groups that I want to target - people who are suffering from stress and anxiety, people who treat them and parents who want to get their kids outside (thereby preventing stress and anxiety)

Contact Information for Business Card

Joan Petrie
Brightmoor
Telephone +44 7700 900417
brightmoor@mailvane.com

Logo Text

Brightmoor - if that. I have an idea that the logo should have a leaf on it somewhere, or maybe just be a leaf.

Coding

Coded - Design and coding required

Number of Pages Required

5+ page

Font styles to use
Serif
Sans Serif

Colors
add136
33b8a4
34a6d7
3377b5

Requirements
Must have
• Space for lots of images. The ability for me to edit the pages if I need to. Be user friendly. Look beautiful.
• For an idea of the images I use and the content I'm interested in writing about have a look at @brightmoor on instagram.
• That pop up about cookies so I am complying with data laws.
Should not have
• Must not be too 'busy' I'd like to avoid too much movement.

```html
<!DOCTYPE html>
<html lang="en">
<head>
<meta charset="utf-8">
<title>Brightmoor – Home page and cookie notice</title>
<link href="https://fonts.googleapis.com/css2?family=Montserrat:wght@400;600;700;800&family=Open+Sans:wght@400;600&family=Lora:wght@600&display=swap" rel="stylesheet">
<style>
:root{
  --green:#add136;
  --teal:#33b8a4;
  --sky:#34a6d7;
  --blue:#3377b5;
  --ink:#2d3a40;
  --muted:#7b858a;
  --stage:#8e9091;
  --white:#ffffff;
  --forest-a:#2f4a2a;
  --forest-b:#6f8f3e;
}
*{box-sizing:border-box;margin:0;padding:0}
html,body{width:813px;height:1200px;overflow:hidden}
body{background:var(--stage);font-family:"Open Sans",Arial,sans-serif;color:var(--ink);position:relative}
.screen{position:absolute;top:15px;width:376px;height:1170px;background:var(--white);overflow:hidden;box-shadow:0 2px 8px rgba(0,0,0,.25)}
.screen--home{left:20px}
.screen--cookies{left:417px}

.hero{height:168px;position:relative;background:linear-gradient(180deg,#1f3320 0%,var(--forest-a) 40%,var(--forest-b) 100%);text-align:center;color:var(--white)}
.hero__nav{position:absolute;top:8px;left:12px;right:12px;display:flex;justify-content:space-between;align-items:center;font-size:5px;font-family:Montserrat,sans-serif}
.hero__brand{font-weight:700;font-size:7px;display:flex;align-items:center;gap:3px}
.hero__brand i{width:6px;height:6px;border-radius:50%;background:var(--green);display:block}
.hero__menu{display:flex;gap:7px;opacity:.9}
.hero__title{position:absolute;top:68px;left:0;right:0;font-family:Montserrat,sans-serif;font-weight:800;font-size:12px;letter-spacing:.3px}
.btn{display:inline-block;font-family:Montserrat,sans-serif;font-weight:700;font-size:5px;color:var(--white);background:var(--blue);border-radius:8px;padding:4px 10px;letter-spacing:.3px}
.hero .btn{position:absolute;top:104px;left:50%;transform:translateX(-50%);background:var(--sky)}

.services{height:475px;padding:22px 26px 0}
.service{display:flex;gap:16px;align-items:center;height:150px}
.service--flip{flex-direction:row-reverse}
.service__photo{width:130px;height:90px;flex:none}
.photo-lake{background:linear-gradient(180deg,#6d8fb0,#9fb8c9 55%,#5d7a8f)}
.photo-coast{background:linear-gradient(160deg,#a9b9c4,#6b6558 60%,#3f3a33)}
.photo-woods{background:linear-gradient(170deg,#3b4a3c,#7c8a73 60%,#55604e)}
.service__title{font-family:Montserrat,sans-serif;font-weight:800;font-size:10px;color:var(--blue);margin-bottom:5px}
.service__title span{color:var(--sky)}
.service__text{font-size:4.6px;line-height:1.6;color:var(--muted);margin-bottom:7px}
.service .btn{font-size:4.5px;padding:3px 9px}

.pillars{height:45px;background:var(--teal);display:flex;justify-content:space-around;align-items:center;padding:0 18px}
.pillar{display:flex;flex-direction:column;align-items:center;gap:3px;color:var(--white);font-size:4px;font-family:Montserrat,sans-serif}
.pillar svg{width:14px;height:14px}

.testimonial{height:157px;text-align:center;padding-top:34px}
.testimonial__avatar{width:22px;height:22px;border-radius:50%;background:linear-gradient(135deg,#c9a98a,#7d6550);margin:0 auto 12px}
.testimonial__quote{font-size:4.8px;line-height:1.7;color:var(--muted);width:250px;margin:0 auto;font-style:italic}
.testimonial__name{font-size:4.5px;font-weight:600;color:var(--ink);margin-top:6px}

.about{height:130px;position:relative;background:linear-gradient(90deg,#3a3046 0%,#6b5563 45%,#a46e5c 100%);color:var(--white)}
.about__person{position:absolute;left:36px;bottom:0;width:70px;height:112px;background:linear-gradient(180deg,#5b3f6e,#3b2a47);border-radius:30px 30px 0 0;opacity:.8}
.about__body{position:absolute;left:150px;top:30px;width:190px}
.about__title{font-family:Montserrat,sans-serif;font-weight:800;font-size:10px;color:var(--green);margin-bottom:5px}
.about__text{font-size:4.6px;line-height:1.6;margin-bottom:8px}

.newsletter{height:87px;background:linear-gradient(90deg,var(--blue),var(--sky));text-align:center;color:var(--white);padding-top:20px}
.newsletter__title{font-family:Montserrat,sans-serif;font-size:10px;font-weight:400;letter-spacing:.4px}
.newsletter__title b{font-weight:800}
.newsletter__lead{font-size:4.4px;margin:4px 0 9px;opacity:.9}
.newsletter__form{display:flex;justify-content:center;gap:5px}
.field{width:78px;height:11px;background:var(--white);border-radius:2px}
.newsletter .btn{background:var(--green);border-radius:2px;padding:3px 9px}

.footer{height:108px;display:flex;justify-content:space-between;padding:22px 26px}
.footer__brand{font-family:Lora,serif;font-weight:600;font-size:9px;color:var(--teal);margin-bottom:10px}
.footer__tag{font-size:5px;font-weight:600;color:var(--ink)}
.footer__social{display:flex;gap:5px;margin-top:6px}
.footer__social span{width:6px;height:6px;border-radius:50%;background:var(--blue)}
.footer__cols{display:flex;gap:22px}
.footer__col{list-style:none;font-size:4.4px;line-height:2;color:var(--muted)}

.overlay{position:absolute;inset:0;background:rgba(20,25,30,.55)}
.cookie{position:absolute;top:58px;left:103px;width:170px;background:var(--white);border-radius:3px;padding:10px 12px;text-align:center;box-shadow:0 2px 6px rgba(0,0,0,.3)}
.cookie__title{font-family:Montserrat,sans-serif;font-weight:700;font-size:5.5px;margin-bottom:4px}
.cookie__text{font-size:3.8px;line-height:1.6;color:var(--muted);margin-bottom:6px}
.cookie__actions{display:flex;justify-content:center;gap:6px}
.cookie__actions .btn{font-size:4px;padding:3px 8px;border-radius:2px}
.btn--accept{background:var(--teal)}
.btn--decline{background:#555d61}
</style>
</head>
<body>

<!-- Home page -->
<section class="screen screen--home">
  <header class="hero" role="img" aria-label="Forest path under tall trees, sunlight on green undergrowth">
    <nav class="hero__nav"><div class="hero__brand"><i></i>Brightmoor</div><div class="hero__menu"><span>Home</span><span>About</span><span>Services</span><span>Blog</span><span>Contact</span></div></nav>
    <h1 class="hero__title">FIND YOUR HAPPINESS AND LEARN TO LOVE NATURE</h1>
    <span class="btn">READ MORE</span>
  </header>
  <main class="services">
    <article class="service">
      <div class="service__photo photo-lake" role="img" aria-label="Person standing in a calm lake"></div>
      <div><h2 class="service__title">OUTDOOR <span>COACHING</span></h2><p class="service__text">Step outside and talk things through while we walk. Sessions take place in green spaces where calm comes easily and fresh ideas can grow. Find time to slow down, breathe and notice.</p><span class="btn">READ MORE</span></div>
    </article>
    <article class="service service--flip">
      <div class="service__photo photo-coast" role="img" aria-label="Person looking out over the sea"></div>
      <div><h2 class="service__title">OUR <span>RETREATS</span></h2><p class="service__text">Weekend retreats in wild places, with quiet mornings, shared meals and long walks. A chance to rest your mind, reconnect with the seasons and return home feeling lighter.</p><span class="btn">READ MORE</span></div>
    </article>
    <article class="service">
      <div class="service__photo photo-woods" role="img" aria-label="Two walkers on a woodland trail"></div>
      <div><h2 class="service__title">WILDERNESS <span>WALKING</span></h2><p class="service__text">Guided walking workshops for families, groups and carers. Learn simple ways to bring nature into daily life and help children grow happy outdoors.</p><span class="btn">READ MORE</span></div>
    </article>
  </main>
  <section class="pillars">
    <div class="pillar"><svg viewBox="0 0 14 14" fill="none" stroke="#fff" stroke-width="1"><path d="M7 1c4 3 4 8 0 12-4-4-4-9 0-12zM7 4v9"/></svg>Nature</div>
    <div class="pillar"><svg viewBox="0 0 14 14" fill="none" stroke="#fff" stroke-width="1"><circle cx="7" cy="4" r="2"/><path d="M3 13c0-4 8-4 8 0"/></svg>Coaching</div>
    <div class="pillar"><svg viewBox="0 0 14 14" fill="none" stroke="#fff" stroke-width="1"><path d="M1 12l4-7 3 4 2-3 3 6z"/></svg>Retreats</div>
    <div class="pillar"><svg viewBox="0 0 14 14" fill="none" stroke="#fff" stroke-width="1"><circle cx="7" cy="7" r="5.5"/><path d="M4 8c1 2 5 2 6 0"/></svg>Wellbeing</div>
    <div class="pillar"><svg viewBox="0 0 14 14" fill="none" stroke="#fff" stroke-width="1"><path d="M3 13l4-11 4 11M5 8h4"/></svg>Walking</div>
  </section>
  <section class="testimonial">
    <div class="testimonial__avatar" role="img" aria-label="Client portrait"></div>
    <p class="testimonial__quote">“Spending time outdoors with Brightmoor changed how I handle stress. I now walk every morning and feel calmer, clearer and more present with my family than I have in years.”</p>
    <p class="testimonial__name">— Happy client</p>
  </section>
  <section class="about">
    <div class="about__person" role="img" aria-label="Woman in a purple jacket on a hillside at dusk"></div>
    <div class="about__body"><h2 class="about__title">ABOUT BRIGHTMOOR</h2><p class="about__text">Brightmoor shares stories, research and simple habits that show why time in nature matters for good health of body and mind.</p><span class="btn">READ MORE</span></div>
  </section>
  <section class="newsletter">
    <h2 class="newsletter__title">NEWSLETTER <b>SIGN-UP</b></h2>
    <p class="newsletter__lead">Join our list for new posts, walks and retreat dates.</p>
    <div class="newsletter__form"><span class="field"></span><span class="field"></span><span class="btn">SIGN UP</span></div>
  </section>
  <footer class="footer">
    <div><div class="footer__brand">Brightmoor</div><p class="footer__tag">Your Wellbeing Matters</p><div class="footer__social"><span></span><span></span><span></span></div></div>
    <div class="footer__cols"><ul class="footer__col"><li>Home</li><li>About</li><li>Coaching</li><li>Retreats</li></ul><ul class="footer__col"><li>Walking</li><li>Blog</li><li>Contact</li><li>Privacy</li></ul></div>
  </footer>
</section>

<!-- Home page with cookie notice -->
<section class="screen screen--cookies">
  <header class="hero" role="img" aria-label="Forest path under tall trees, sunlight on green undergrowth">
    <nav class="hero__nav"><div class="hero__brand"><i></i>Brightmoor</div><div class="hero__menu"><span>Home</span><span>About</span><span>Services</span><span>Blog</span><span>Contact</span></div></nav>
    <h1 class="hero__title">FIND YOUR HAPPINESS AND LEARN TO LOVE NATURE</h1>
    <span class="btn">READ MORE</span>
  </header>
  <main class="services">
    <article class="service">
      <div class="service__photo photo-lake" role="img" aria-label="Person standing in a calm lake"></div>
      <div><h2 class="service__title">OUTDOOR <span>COACHING</span></h2><p class="service__text">Step outside and talk things through while we walk. Sessions take place in green spaces where calm comes easily and fresh ideas can grow. Find time to slow down, breathe and notice.</p><span class="btn">READ MORE</span></div>
    </article>
    <article class="service service--flip">
      <div class="service__photo photo-coast" role="img" aria-label="Person looking out over the sea"></div>
      <div><h2 class="service__title">OUR <span>RETREATS</span></h2><p class="service__text">Weekend retreats in wild places, with quiet mornings, shared meals and long walks. A chance to rest your mind, reconnect with the seasons and return home feeling lighter.</p><span class="btn">READ MORE</span></div>
    </article>
    <article class="service">
      <div class="service__photo photo-woods" role="img" aria-label="Two walkers on a woodland trail"></div>
      <div><h2 class="service__title">WILDERNESS <span>WALKING</span></h2><p class="service__text">Guided walking workshops for families, groups and carers. Learn simple ways to bring nature into daily life and help children grow happy outdoors.</p><span class="btn">READ MORE</span></div>
    </article>
  </main>
  <section class="pillars">
    <div class="pillar"><svg viewBox="0 0 14 14" fill="none" stroke="#fff" stroke-width="1"><path d="M7 1c4 3 4 8 0 12-4-4-4-9 0-12zM7 4v9"/></svg>Nature</div>
    <div class="pillar"><svg viewBox="0 0 14 14" fill="none" stroke="#fff" stroke-width="1"><circle cx="7" cy="4" r="2"/><path d="M3 13c0-4 8-4 8 0"/></svg>Coaching</div>
    <div class="pillar"><svg viewBox="0 0 14 14" fill="none" stroke="#fff" stroke-width="1"><path d="M1 12l4-7 3 4 2-3 3 6z"/></svg>Retreats</div>
    <div class="pillar"><svg viewBox="0 0 14 14" fill="none" stroke="#fff" stroke-width="1"><circle cx="7" cy="7" r="5.5"/><path d="M4 8c1 2 5 2 6 0"/></svg>Wellbeing</div>
    <div class="pillar"><svg viewBox="0 0 14 14" fill="none" stroke="#fff" stroke-width="1"><path d="M3 13l4-11 4 11M5 8h4"/></svg>Walking</div>
  </section>
  <section class="testimonial">
    <div class="testimonial__avatar" role="img" aria-label="Client portrait"></div>
    <p class="testimonial__quote">“Spending time outdoors with Brightmoor changed how I handle stress. I now walk every morning and feel calmer, clearer and more present with my family than I have in years.”</p>
    <p class="testimonial__name">— Happy client</p>
  </section>
  <section class="about">
    <div class="about__person" role="img" aria-label="Woman in a purple jacket on a hillside at dusk"></div>
    <div class="about__body"><h2 class="about__title">ABOUT BRIGHTMOOR</h2><p class="about__text">Brightmoor shares stories, research and simple habits that show why time in nature matters for good health of body and mind.</p><span class="btn">READ MORE</span></div>
  </section>
  <section class="newsletter">
    <h2 class="newsletter__title">NEWSLETTER <b>SIGN-UP</b></h2>
    <p class="newsletter__lead">Join our list for new posts, walks and retreat dates.</p>
    <div class="newsletter__form"><span class="field"></span><span class="field"></span><span class="btn">SIGN UP</span></div>
  </section>
  <footer class="footer">
    <div><div class="footer__brand">Brightmoor</div><p class="footer__tag">Your Wellbeing Matters</p><div class="footer__social"><span></span><span></span><span></span></div></div>
    <div class="footer__cols"><ul class="footer__col"><li>Home</li><li>About</li><li>Coaching</li><li>Retreats</li></ul><ul class="footer__col"><li>Walking</li><li>Blog</li><li>Contact</li><li>Privacy</li></ul></div>
  </footer>
  <div class="overlay"></div>
  <div class="cookie" role="dialog" aria-label="Cookie notice">
    <p class="cookie__title">Cookies &amp; Privacy</p>
    <p class="cookie__text">We use cookies to give you the best experience on our site. By continuing you agree to our use of cookies as set out in our privacy policy.</p>
    <div class="cookie__actions"><span class="btn btn--accept">ACCEPT</span><span class="btn btn--decline">DECLINE</span></div>
  </div>
</section>

</body>
</html>
```